Business card design/logo/website name

I am a business coach. My business name is KDP (Kessel Dunmore & Partners, Inc.) I want to use this card just for coaching. I do two kinds: Personal Image coach and Executive business coach
1. I work with people to become a polished global professional.
"Become a confident, savvy professional building relationships tactfully and appropriately while clearly representing your own company’s message and image.
Learn the nuances… Master the skills… Use the business etiquette techniques and protocols that allow you to seamlessly and confidently conduct business in a global business environment.
Have the comfort of knowing what to expect, what to do and how to easily build long and short-term relationships that give you the winning edge and increased company profits."
2. Leadership Coaching
For increasing the team’s productivity by building stronger relationships. Build strong compelling vision and write and share their Personal Leadership Philosophy, a roadmap that is concise and commanding and gives the team a clear vision of the leader's expectations.
Updates

KDP should be the logo. (Downplay the Kessel Dunmore and Partners, Inc.)

Want:
Executive Coach
Consultant

Reason: I am traveling and connections are often broken.

Target Market(s)

Executives, business people

Industry/Entity Type

Building

Font styles to use
Sans Serif
Script

Colors
0255a3
3176b5
85acd3
ec2027

Requirements
Must have
• KDP as the logo,(no preference on how you treat KDP) with Kessel Dunmore & Partners. Inc. downplayed.
On the card:
Rosalind Dunmore CEO
Executive Coach
Consultant
KRC 4(c)
Coaching - Training - Strategic Planning

```html
<!DOCTYPE html>
<html lang="en">
<head>
<meta charset="utf-8">
<title>KDP – Rosalind Dunmore Business Card</title>
<link rel="stylesheet" href="https://fonts.googleapis.com/css2?family=Michroma&family=Open+Sans:wght@400;600;700&display=swap">
<style>
  :root {
    --backdrop: #2e2e31;
    --card-top: #fbfbfb;
    --card-bottom: #e4e4e6;
    --brand: #0255a3;
    --brand-mid: #3176b5;
    --brand-light: #85acd3;
    --accent: #ec2027;
    --ink: #232326;
    --paper: #ffffff;
  }
  * { margin: 0; padding: 0; box-sizing: border-box; }
  html, body {
    width: 1200px; height: 816px; overflow: hidden;
    background: var(--backdrop);
  }
  .card {
    position: absolute; left: 100px; top: 122px;
    width: 1000px; height: 572px;
    border-radius: 44px; overflow: hidden;
    background: linear-gradient(160deg, var(--card-top) 0%, #f1f1f2 55%, var(--card-bottom) 100%);
    font-family: "Open Sans", Arial, sans-serif;
  }
  .card__band { position: absolute; left: 0; top: 0; width: 1000px; height: 572px; }

  .brand { position: absolute; left: 560px; top: 92px; width: 400px; }
  .brand__mark {
    display: flex; align-items: center; gap: 18px;
    font-family: "Michroma", "Arial Black", sans-serif;
    font-weight: 400; font-size: 78px; line-height: 96px;
    color: var(--brand); letter-spacing: 4px;
  }
  .brand__dot { width: 18px; height: 18px; background: var(--accent); flex: none; }
  .brand__legal {
    margin-top: 14px;
    font-family: "Michroma", "Arial Black", sans-serif;
    font-size: 15px; line-height: 22px; color: var(--brand-mid); letter-spacing: 0.5px;
  }
  .brand__cert {
    margin-top: 6px;
    font-size: 17px; font-weight: 600; line-height: 24px; color: var(--brand-mid);
  }

  .person { position: absolute; left: 58px; top: 150px; }
  .person__name {
    font-weight: 700; font-size: 33px; color: var(--brand);
    letter-spacing: 0.3px; line-height: 40px;
  }
  .person__role { font-weight: 600; font-size: 25px; color: var(--brand-mid); line-height: 32px; }
  .person__skills { font-weight: 400; font-size: 21px; color: var(--brand-mid); line-height: 30px; }

  .contact { position: absolute; left: 54px; top: 300px; list-style: none; }
  .contact__item {
    display: flex; align-items: flex-start; gap: 12px;
    font-size: 22px; line-height: 30px; color: var(--ink);
  }
  .contact__item--address { font-weight: 700; margin-bottom: 4px; }
  .contact__icon { width: 22px; height: 30px; flex: none; fill: var(--brand); }

  .website {
    position: absolute; left: 508px; top: 410px; width: 470px;
    text-align: center; font-size: 30px; line-height: 40px; color: var(--paper); letter-spacing: 0.3px;
  }
  .tagline {
    position: absolute; left: 58px; top: 516px;
    font-size: 22px; font-weight: 600; line-height: 30px; color: var(--paper); letter-spacing: 0.3px;
  }
</style>
</head>
<body>
<main class="card" aria-label="Business card">
  <svg class="card__band" viewBox="0 0 1000 572" aria-hidden="true">
    <path d="M0 494 H470 C500 494 500 470 500 440 H1000 V572 H0 Z" fill="var(--brand)"/>
    <rect x="482" y="386" width="560" height="96" rx="48" fill="var(--brand)" stroke="var(--paper)" stroke-width="5"/>
    <rect x="0" y="488" width="470" height="3" fill="var(--brand-light)"/>
  </svg>

  <header class="brand">
    <p class="brand__mark"><span class="brand__dot"></span>KDP</p>
    <p class="brand__legal">Kessel Dunmore &amp; Partners, Inc.</p>
    <p class="brand__cert">KRC 4(c)</p>
  </header>

  <section class="person">
    <p class="person__name">ROSALIND DUNMORE</p>
    <p class="person__role">CEO</p>
    <p class="person__skills">Executive Coach · Consultant</p>
  </section>

  <ul class="contact">
    <li class="contact__item contact__item--address">
      <svg class="contact__icon" viewBox="0 0 22 30"><path d="M11 4a7 7 0 0 0-7 7c0 5 7 13 7 13s7-8 7-13a7 7 0 0 0-7-7zm0 9.5a2.6 2.6 0 1 1 0-5.2 2.6 2.6 0 0 1 0 5.2z"/></svg>
      <span>214.12th floor,Harbor Crest<br>Road NVT</span>
    </li>
    <li class="contact__item">
      <svg class="contact__icon" viewBox="0 0 22 30"><path d="M3 13c0-3 4-5 8-5s8 2 8 5v2h-4v-2c-1-1-7-1-8 0v2H3zM6 17h10l2 5H4z"/></svg>
      <span>021 555 0148</span>
    </li>
    <li class="contact__item">
      <svg class="contact__icon" viewBox="0 0 22 30"><path d="M6 7h8l2 2v4H6zM4 14h14v9H4zm3 3v2h2v-2zm4 0v2h2v-2z"/></svg>
      <span>021 555 0149</span>
    </li>
    <li class="contact__item">
      <svg class="contact__icon" viewBox="0 0 22 30"><path d="M3 10h16v11H3zm1.5 1.5L11 16.5l6.5-5z" fill-rule="evenodd"/></svg>
      <span>yourname@mailbox.com</span>
    </li>
  </ul>

  <p class="website">www.yoursitename.com</p>
  <p class="tagline">Coaching - Training - Strategic Planning</p>
</main>
</body>
</html>
```